Marta's Dwellings website

We need a simple website for our property investment business in the UK. We basically need our contact details and brief description.We have the company logo already done (via ArtFlockly) so please use these:https://drive.google.com/drive/folders/1szJ3iRhelElZ40NIFT7w-c14MaY3Y_oV?usp=sharingYou could use some stock photos of UK houses for now.Let me know when to provide more detailed descriptions, etc

Coding

Coded - Design and coding required

Number of Pages Required

1 page

Colors

Designer to choose colors to be used in the design.

```html
<!DOCTYPE html>
<html lang="en">
<head>
<meta charset="utf-8">
<title>Marta's Dwellings</title>
<link rel="stylesheet" href="https://fonts.googleapis.com/css2?family=Questrial&family=Poppins:wght@300;400&display=swap">
<style>
:root{
  --sky:#3f6aa6;
  --ink:#1b1b1b;
  --card:#151719;
  --blue:#3b69a3;
  --white:#ffffff;
  --text:#3a3a3a;
  --muted:#bdbdbd;
}
*{margin:0;padding:0;box-sizing:border-box}
html,body{width:1200px;height:3632px;overflow:hidden;background:var(--white)}
body{position:relative;font-family:"Poppins",sans-serif;color:var(--text)}
h1,h2,h3,h4{font-weight:400}
.abs{position:absolute}
.heading{font-family:"Questrial",sans-serif;font-weight:400;letter-spacing:3px;color:var(--ink)}
.body-copy{font-size:11.5px;line-height:24px;font-weight:300}
.btn{display:inline-flex;border:1.5px solid var(--ink);font-size:12.5px;align-items:center;justify-content:center;color:var(--ink)}
.btn-abs{position:absolute}

/* hero */
.hero-photo{left:0;top:0;width:1200px;height:680px}
.topbar{left:0;top:0;width:1200px;height:131px;border-bottom:1px solid rgba(255,255,255,.25)}
.phone{left:172px;top:28px;color:var(--white);font-family:"Questrial",sans-serif;font-size:16px;letter-spacing:1px;display:flex;align-items:center;gap:8px}
.search{left:842px;top:44px;width:183px;border-bottom:1px solid rgba(255,255,255,.5)}
.search svg{position:absolute;right:0;top:-16px}
.nav a{position:absolute;top:84px;color:var(--white);font-family:"Questrial",sans-serif;font-size:15px;letter-spacing:1.5px;text-decoration:none}
.nav .active::after{content:"";position:absolute;left:0;top:42px;width:44px;height:3px;background:var(--white)}
.brand{left:450px;top:30px;width:300px;text-align:center;color:var(--white)}
.brand .mark{display:block;width:34px;height:34px;margin:0 auto 14px;background:var(--white)}
.brand .name{font-family:"Questrial",sans-serif;font-size:11px;letter-spacing:6px}
.welcome{left:351px;top:312px;width:498px;height:66px;background:rgba(15,15,15,.82);color:var(--white);font-family:"Questrial",sans-serif;font-size:29px;letter-spacing:3px;display:flex;align-items:center;justify-content:center}
.dots{left:519px;top:590px;display:flex;gap:4px}
.dots span{width:37px;height:4px;background:var(--ink)}
.dots span.on{background:var(--white)}

/* about */
.about-back{left:172px;top:771px;width:254px;height:326px;background:linear-gradient(160deg,#2d3340,#4d4637)}
.about-front{left:300px;top:813px;width:294px;height:335px;background:var(--white);padding:6px}
.about-front div{width:100%;height:100%;background:linear-gradient(180deg,#b9cbe0 0%,#a2542f 40%,#8a4226 75%,#556b35 100%)}
.about-text{left:647px;top:780px;width:380px}
.about-text h2{font-size:34px;line-height:34px}
.about-text p{margin-top:18px;width:372px}
.about-text .btn{margin-top:12px;width:98px;height:35px}

/* services */
.services-title{left:0;top:1305px;width:1200px;text-align:center;font-size:35px;color:var(--white)}
.card{top:1437px;width:265px;height:251px;background:rgba(12,13,14,.78);border:1px solid rgba(255,255,255,.12);text-align:center;color:var(--white)}
.card .ring{position:absolute;left:86px;top:-44px;width:92px;height:92px;border-radius:50%;background:rgba(50,52,56,.9);display:flex;align-items:center;justify-content:center}
.card .ring div{width:80px;height:80px;border-radius:50%;background:#111;display:flex;align-items:center;justify-content:center}
.card h3{position:absolute;top:70px;width:100%;font-size:21px}
.card p{position:absolute;top:106px;left:18px;right:18px;font-size:11.5px;line-height:20.5px;color:var(--muted);font-weight:300;letter-spacing:.3px}

/* property */
.prop-title{left:0;top:1833px;width:1200px;text-align:center;font-size:35px}
.prop-img{top:1920px;width:412px;height:243px}
.prop-name{top:2180px;font-family:"Questrial",sans-serif;font-weight:400;font-size:23px;color:var(--ink)}
.prop-copy{top:2219px;width:412px}

/* contact */
.contact-text{left:173px;top:2533px;width:390px;color:var(--white)}
.contact-text h2{font-size:34px;line-height:34px;color:var(--white)}
.contact-text p{width:380px}
.contact-text .btn{margin-top:14px;width:99px;height:34px;border-color:var(--white);color:var(--white)}
.portrait-frame{left:619px;top:2545px;width:378px;height:372px;border:3px solid var(--white)}
.portrait{left:639px;top:2510px;width:389px;height:389px;background:linear-gradient(160deg,#8d8c8a,#55524f 60%,#26252a)}

/* map & address */
.map{left:0;top:2990px;width:1200px;height:440px;background:linear-gradient(180deg,#eceef1,#e4e7ea)}
.address{left:572px;top:3103px;width:206px;height:236px;background:var(--white);border:2px solid var(--ink);padding:30px 0 0 24px}
.address h4{font-size:26px;margin-bottom:12px}
.address p{font-family:"Questrial",sans-serif;font-size:14px;line-height:23.5px;letter-spacing:1.2px;color:var(--ink)}

/* footer */
.footer{left:0;top:3430px;width:1200px;height:202px;background:#000;color:var(--white);text-align:center}
.footer .mark{display:block;width:34px;height:34px;margin:34px auto 14px;background:var(--white)}
.footer .name{font-family:"Questrial",sans-serif;font-size:10px;letter-spacing:6px}
.socials{display:flex;justify-content:center;gap:10px;margin-top:22px}
.socials span{width:30px;height:30px;border-radius:50%;background:#2a2a2a;border:1px solid #555}
.copyright{margin-top:20px;font-size:11px}
</style>
</head>
<body>

<header>
  <div class="abs hero-photo" role="img" aria-label="Photograph of a red brick detached house with a tiled roof and white garage doors under a blue sky" style="background:linear-gradient(180deg,#3e6cab 0%,#6f91bf 22%,#9a6247 45%,#a04e2d 65%,#7f7b72 80%,#6c8a3b 100%)"></div>
  <svg class="abs" style="left:0;top:600px" width="1200" height="90" viewBox="0 0 1200 90" aria-hidden="true"><polygon points="0,80 1200,20 1200,90 0,90" fill="#fff"/></svg>
  <div class="abs topbar"></div>
  <div class="abs phone">
    <svg width="14" height="14" viewBox="0 0 24 24" aria-hidden="true"><path fill="#fff" d="M6.6 10.8a15.1 15.1 0 0 0 6.6 6.6l2.2-2.2c.3-.3.7-.4 1-.2 1.1.4 2.3.6 3.6.6.6 0 1 .4 1 1V20c0 .6-.4 1-1 1A17 17 0 0 1 3 4c0-.6.4-1 1-1h3.5c.6 0 1 .4 1 1 0 1.3.2 2.5.6 3.6.1.3 0 .7-.2 1z"/></svg>
    Cal: 140 388 2917
  </div>
  <div class="abs search"><svg width="16" height="16" viewBox="0 0 24 24" aria-hidden="true"><circle cx="10" cy="10" r="7" fill="none" stroke="#fff" stroke-width="3"/><line x1="15" y1="15" x2="22" y2="22" stroke="#fff" stroke-width="3"/></svg></div>
  <nav class="nav">
    <a class="active" style="left:172px" href="#">Home</a>
    <a style="left:272px" href="#">About</a>
    <a style="left:371px" href="#">Investment</a>
    <a style="left:745px" href="#">Property</a>
    <a style="left:871px" href="#">News</a>
    <a style="left:963px" href="#">Contact</a>
  </nav>
  <div class="abs brand"><span class="mark"></span><span class="name">MARTA'S DWELLINGS</span></div>
  <div class="abs welcome">Welcome to Marta's Dwellings</div>
  <div class="abs dots"><span class="on"></span><span></span><span></span><span></span></div>
</header>

<section class="about">
  <div class="abs about-back" role="img" aria-label="Photograph of a stone terraced house at dusk"></div>
  <div class="abs about-front" role="img" aria-label="Photograph of a red brick house with white windows"><div></div></div>
  <div class="abs about-text">
    <h2 class="heading">About<br>Marta's Dwellings</h2>
    <p class="body-copy">Sed ut perspiciatis unde omnis iste natus error sit voluptatem accusantium doloremque laudantium, totam rem aperiaque ipsa quae ab illo inventore veritatis et quasi architecto beatae vitae dicta sunt explicabo. Nemo enim ipsam voluptatem quia voluptas sit aspernatur aut odit aut fugit, sed quia consequuntur magni dolores eos qui ratione voluptatem sequi nesciunteque porro quisquam est, qui dolorem ipsum quia dolor sit amet, consectetur, adipisci velit, sed quia non numquam eius modi tempora incidunt ut labore et dolore magnam</p>
    <div class="btn">Read More</div>
  </div>
</section>

<section class="services">
  <svg class="abs" style="left:0;top:1213px" width="1200" height="610" viewBox="0 0 1200 610" role="img" aria-label="Dimmed aerial photograph of a town of red brick houses">
    <defs><linearGradient id="townShade" x1="0" y1="0" x2="0" y2="1"><stop offset="0" stop-color="#2c2f33"/><stop offset=".5" stop-color="#24272a"/><stop offset="1" stop-color="#2e2a28"/></linearGradient></defs>
    <polygon points="0,49 1200,0 1200,558 0,609" fill="url(#townShade)"/>
  </svg>
  <h2 class="abs heading services-title">What We Do</h2>
  <div class="abs card" style="left:172px">
    <div class="ring"><div><svg width="44" height="44" viewBox="0 0 44 44" aria-hidden="true" fill="none" stroke="#fff" stroke-width="2"><path d="M6 22 22 8l16 14"/><path d="M11 18v18h22V18"/><rect x="18" y="24" width="8" height="12"/></svg></div></div>
    <h3 class="heading" style="color:#fff">Spersicloema</h3>
    <p>Sed ut perspiciatis undeomtus errloreor sitvoluptem accusantium dolor emqlorue laudantium, toteria aquesauae ab illo ine laudantium, toteria aquesauae ab tore.</p>
  </div>
  <div class="abs card" style="left:467px">
    <div class="ring"><div><svg width="44" height="44" viewBox="0 0 44 44" aria-hidden="true" fill="none" stroke="#fff" stroke-width="2"><circle cx="23" cy="17" r="9"/><path d="M23 12v10M20 14h5a2 2 0 0 1 0 3h-4a2 2 0 0 0 0 3h5"/><path d="M6 36h8l8-4h10"/><path d="M6 30h6l6 2"/></svg></div></div>
    <h3 class="heading" style="color:#fff">Spersicloema</h3>
    <p>Sed ut perspiciatis undeomtus errloreor sitvoluptem accusantium dolor emqlorue laudantium, toteria aquesauae ab illo ine laudantium, toteria aquesauae ab tore.</p>
  </div>
  <div class="abs card" style="left:760px">
    <div class="ring"><div><svg width="44" height="44" viewBox="0 0 44 44" aria-hidden="true" fill="none" stroke="#fff" stroke-width="2"><rect x="8" y="28" width="5" height="8"/><rect x="16" y="23" width="5" height="13"/><rect x="24" y="19" width="5" height="17"/><path d="M8 20 18 12l6 4 10-9M29 7h5v5"/><circle cx="34" cy="31" r="5"/></svg></div></div>
    <h3 class="heading" style="color:#fff">Spersicloema</h3>
    <p>Sed ut perspiciatis undeomtus errloreor sitvoluptem accusantium dolor emqlorue laudantium, toteria aquesauae ab illo ine laudantium, toteria aquesauae ab tore.</p>
  </div>
</section>

<section class="property">
  <h2 class="abs heading prop-title">Our Property</h2>
  <div class="abs prop-img" style="left:172px;background:linear-gradient(180deg,#6f9ad6 0%,#b7c9de 30%,#8d4a34 55%,#5c7f2e 100%)" role="img" aria-label="Photograph of a row of Victorian red brick terraced houses on a hill"></div>
  <div class="abs prop-img" style="left:615px;background:linear-gradient(180deg,#6e9fdc 0%,#6c6a68 30%,#8e4332 55%,#7a3a2d 85%,#6b7d45 100%)" role="img" aria-label="Photograph of a two storey red brick house with a grey tiled roof"></div>
  <h3 class="abs prop-name" style="left:170px">Doloremque lauantium</h3>
  <h3 class="abs prop-name" style="left:614px">Doloremque lauantium</h3>
  <p class="abs body-copy prop-copy" style="left:172px">Sed ut perspiciatis unde omnis iste natus error sit voluptatem acs ntium doloremque laudantium, totam rem aperiaque psa quaelo inventore veritatis et quasi architecto beatplicabemo eni ipsam voluptatem quia voluptas sit aspernatu.</p>
  <p class="abs body-copy prop-copy" style="left:615px">Sed ut perspiciatis unde omnis iste natus error sit voluptatem acs ntium doloremque laudantium, totam rem aperiaque psa quaelo inventore veritatis et quasi architecto beatplicabemo eni ipsam voluptatem quia voluptas sit aspernatu.</p>
</section>

<section class="contact">
  <div class="abs map" role="img" aria-label="Street map of the office neighbourhood"></div>
  <svg class="abs" style="left:0;top:2380px" width="1200" height="675" viewBox="0 0 1200 675" role="img" aria-label="Blue tinted photograph of a house facade">
    <polygon points="0,0 1200,27 1200,673 0,630" fill="#3b69a3"/>
  </svg>
  <div class="abs contact-text">
    <h2 class="heading">Contact<br>Marta Louise Grey</h2>
    <p class="body-copy">Sed ut perspiciatis unde omnis iste natus error sit voluptatem accusantium doloremque laudantium, totam rem aperiaque ipsa quae ab illo inventore veritatis et quasi architecto beatae vitae dicta sunt explicabo. Nemo enim ipsam voluptatem quia voluptas sit aspernatur aut odit aut fugit, sed quia consequuntur magni dolores eos qui ratione voluptatem sequi nesciunteque porro quisquam est, qui dolorem ipsum quia dolor sit amet, consectetur, adipisci velit, sed quia non numquam eius modi tempora incidunt ut labore et dolore magnam</p>
    <div class="btn">Read More</div>
  </div>
  <div class="abs portrait-frame"></div>
  <div class="abs portrait" role="img" aria-label="Portrait photograph of the company director in a dark blazer"></div>
  <div class="abs address">
    <h4 class="heading">Address</h4>
    <p>Unit 7, Orchard House,<br>12-14 Willow Row,<br>Eastbridge,<br>Ashfordshire,<br>United Kingdom,<br>EB4 7QL</p>
  </div>
</section>

<footer class="abs footer">
  <span class="mark"></span>
  <div class="name">MARTA'S DWELLINGS</div>
  <div class="socials"><span></span><span></span><span></span><span></span></div>
  <p class="copyright">Copyright 2019 Marta's Dwellings.All Rights Reserved</p>
</footer>

</body>
</html>
```